Business Card Design for Online Gift Business

Business card design for a new online Canadian company called "Harlow & Brine Gift Boxes" selling modern and luxurious gift boxes for every occasion. Items are sourced locally from talented socially-responsible Canadian artisans. Each gift is elegantly presented in a keepsake wood box to ensure a lasting impression.

Industry/Entity Type

E-Commerce

Contact Information for Business Card

Marla Whitcombe, Proprietor
Calgary, AB
403-555-2741
www.harlowandbrine.ca
hello@harlowandbrine.ca

Requirements
Must have
• Gifts from our best, to your best
• Please also include the symbols for Facebook and Instagram
Nice to have
• **I have attached a few samples of background colors and font colors that I like. I hope this helps in a few directions to try.

```html
<!DOCTYPE html>
<html lang="en">
<head>
<meta charset="utf-8">
<title>Harlow &amp; Brine Gift Boxes — Business Card</title>
<link href="https://fonts.googleapis.com/css2?family=Arimo:wght@400;700&display=swap" rel="stylesheet">
<style>
  :root {
    --stage: #2b2b2b;
    --card-dark: #5a5a5a;
    --card-light: #ffffff;
    --gold: #bca880;
    --ink-light: #ffffff;
    --ink-muted: #d9d9d9;
  }
  * { box-sizing: border-box; margin: 0; padding: 0; }
  html, body {
    width: 1200px; height: 950px; overflow: hidden;
    background: var(--stage);
    font-family: "Arimo", Arial, sans-serif;
  }
  .stage {
    position: relative; width: 1200px; height: 950px;
    display: flex; flex-direction: column; align-items: center; justify-content: center; gap: 60px;
  }
  .card {
    position: relative; width: 630px; height: 360px; overflow: hidden;
    box-shadow: 0 10px 30px rgba(0,0,0,.45);
  }
  .card--front { background: var(--card-dark); }
  .card--back { background: var(--card-light); }

  .brand {
    display: flex; align-items: center; gap: 14px;
    font-weight: 400; letter-spacing: 2px; white-space: nowrap;
  }
  .brand__dot { width: 14px; height: 14px; border-radius: 50%; flex: none; }
  .card--front .brand {
    position: absolute; left: 0; right: 0; top: 110px; justify-content: center;
    font-size: 44px; color: var(--ink-light);
  }
  .card--front .brand__dot { background: var(--ink-light); }
  .front__tagline {
    position: absolute; left: 0; right: 0; top: 184px; text-align: center;
    color: var(--ink-light); font-size: 17px; letter-spacing: 1px;
  }
  .front__web {
    position: absolute; left: 0; right: 0; top: 258px; text-align: center;
    color: var(--ink-muted); font-size: 15px; letter-spacing: 4px;
  }

  .back__swoosh { position: absolute; inset: 0; width: 100%; height: 100%; }
  .card--back .brand {
    position: absolute; left: 50px; top: 95px;
    font-size: 36px; color: var(--gold);
  }
  .card--back .brand__dot { background: var(--gold); }
  .contact {
    position: absolute; right: 26px; bottom: 18px; text-align: right;
    color: var(--ink-light); line-height: 1.4;
  }
  .contact__name { font-weight: 700; font-size: 20px; }
  .contact__role, .contact__phone, .contact__email { font-size: 15px; }
  .contact__phone b { font-weight: 700; }
  .contact__line { font-size: 13px; margin-top: 2px; }
  .social {
    display: flex; justify-content: flex-end; align-items: center; gap: 6px;
    font-size: 13px; margin-top: 4px;
  }
  .social__mark { width: 12px; height: 12px; border-radius: 50%; background: var(--ink-light); flex: none; }
  .social__mark--square { border-radius: 3px; margin-left: 2px; }
</style>
</head>
<body>
<main class="stage">
  <section class="card card--front" aria-label="Card front">
    <div class="brand"><span class="brand__dot"></span>Harlow &amp; Brine</div>
    <p class="front__tagline">Gifts from our best, to your best</p>
    <p class="front__web">www.harlowandbrine.ca</p>
  </section>

  <section class="card card--back" aria-label="Card back">
    <svg class="back__swoosh" viewBox="0 0 630 360" preserveAspectRatio="none" aria-hidden="true">
      <path d="M500 0 L630 0 L630 360 L0 360 L0 290 C200 320 440 240 500 0 Z" fill="var(--gold)"/>
      <path d="M545 0 C530 170 410 300 200 345 C420 285 535 170 555 0 Z" fill="var(--card-light)"/>
    </svg>
    <div class="brand"><span class="brand__dot"></span>Harlow &amp; Brine</div>
    <div class="contact">
      <p class="contact__name">Marla Whitcombe</p>
      <p class="contact__role">Proprietor</p>
      <p class="contact__phone"><b>P :</b> 403-555-2741</p>
      <p class="contact__email">hello@harlowandbrine.ca</p>
      <p class="contact__line">Calgary, AB | www.harlowandbrine.ca</p>
      <p class="social"><span class="social__mark" aria-hidden="true"></span><span class="social__mark social__mark--square" aria-hidden="true"></span>@harlowandbrine</p>
    </div>
  </section>
</main>
</body>
</html>
```